Bry7Legal Letterhead

Need a new letterhead for my law firm.
IDENTIFYING INFORMATION BELOW:
Anselmo R Quintara III
Attorney at Law
Address: 2847 Larkspur Blvd, Ste 300, Dallas, TX 75204
Phone: 877-482-6017
Fax: 469-738-1452
Email: bry@bry7legal.example
Website: www.bry7legal.example

Colors
0054AA
0677BA
7BADD7
CADEEF
E8F1F8

Requirements
Must have
• Logo needs to be on the letterhead, along with identifying information which is included in the project description.

```html
<!DOCTYPE html>
<html lang="en">
<head>
<meta charset="utf-8">
<title>Bry7Legal Letterhead</title>
<link href="https://fonts.googleapis.com/css2?family=Montserrat:wght@800&family=Open+Sans:wght@400;600&display=swap" rel="stylesheet">
<style>
  :root {
    --brand-navy: #0054AA;
    --brand-blue: #0677BA;
    --brand-sky: #7BADD7;
    --brand-mist: #CADEEF;
    --brand-ice: #E8F1F8;
    --ink: #1c1c1c;
    --body-text: #4a4a4a;
    --paper: #ffffff;
    --band-dark: #111111;
  }
  * { margin: 0; padding: 0; box-sizing: border-box; }
  html, body { width: 784px; height: 1200px; overflow: hidden; background: var(--paper); }
  .letterhead {
    position: relative;
    width: 784px;
    height: 1200px;
    background: var(--paper);
    font-family: "Open Sans", Arial, sans-serif;
    color: var(--body-text);
    overflow: hidden;
  }
  .accent-shapes { position: absolute; top: 0; right: 0; }
  .brand { position: absolute; top: 62px; left: 64px; }
  .brand-name {
    font-family: "Open Sans", Arial, sans-serif;
    font-weight: 600;
    font-size: 38px;
    color: var(--ink);
    line-height: 1.1;
  }
  .brand-tagline {
    margin-top: 6px;
    font-family: "Open Sans", Arial, sans-serif;
    font-weight: 400;
    font-size: 13px;
    letter-spacing: 2px;
    color: var(--brand-blue);
    text-transform: uppercase;
  }
  .letter-body {
    position: absolute;
    top: 220px;
    left: 64px;
    width: 656px;
    font-size: 13px;
    line-height: 1.75;
    text-align: justify;
  }
  .salutation { font-weight: 600; color: var(--ink); margin-bottom: 22px; text-align: left; }
  .letter-body p + p { margin-top: 18px; }
  .signature {
    position: absolute;
    top: 640px;
    right: 64px;
    text-align: right;
  }
  .signature-name {
    font-family: "Montserrat", Arial, sans-serif;
    font-weight: 800;
    font-size: 22px;
    color: var(--brand-navy);
    letter-spacing: 0.3px;
  }
  .signature-title { margin-top: 4px; font-size: 13px; color: var(--body-text); }
  .footer-band { position: absolute; left: 0; bottom: 0; }
  .contact-list {
    position: absolute;
    left: 64px;
    bottom: 44px;
    list-style: none;
    color: #ffffff;
    font-size: 12px;
  }
  .contact-list li { display: flex; align-items: center; gap: 10px; height: 24px; }
  .contact-icon { width: 16px; height: 16px; flex: none; }
</style>
</head>
<body>
<main class="letterhead">
  <svg class="accent-shapes" width="300" height="220" viewBox="0 0 300 220" aria-hidden="true">
    <polygon points="120,0 300,0 300,140" fill="var(--brand-ice)"/>
    <polygon points="200,0 300,0 300,70" fill="var(--brand-mist)" opacity="0.6"/>
  </svg>

  <header class="brand">
    <div class="brand-name">Bry7Legal</div>
    <div class="brand-tagline">Law Office · Dallas</div>
  </header>

  <section class="letter-body">
    <p class="salutation">Dear Sir,</p>
    <p>This sample paragraph stands in for the opening of a letter, showing how copy fills the measure across the page and how lines wrap at a steady rhythm.</p>
    <p>A second block of filler text continues here so the page reads as a full letter, with enough words to run over several lines in the same width.</p>
    <p>A third paragraph keeps the tone calm and plain, leading toward a closing thought before the sign-off.</p>
    <p>If you have any questions, please call our office. Thank you for your time.</p>
  </section>

  <section class="signature">
    <div class="signature-name">ANSELMO R QUINTARA III</div>
    <div class="signature-title">Attorney at Law</div>
  </section>

  <svg class="footer-band" width="784" height="330" viewBox="0 0 784 330" aria-hidden="true">
    <path d="M0,60 C280,110 540,10 784,-10 L784,330 L0,330 Z" fill="var(--brand-sky)"/>
    <path d="M0,84 C280,132 540,34 784,14 L784,330 L0,330 Z" fill="var(--brand-blue)"/>
    <path d="M0,106 C280,150 540,58 784,38 L784,330 L0,330 Z" fill="var(--paper)"/>
    <path d="M0,114 C280,158 540,68 784,48 L784,330 L0,330 Z" fill="var(--band-dark)"/>
  </svg>

  <ul class="contact-list">
    <li>
      <svg class="contact-icon" viewBox="0 0 16 16"><circle cx="8" cy="8" r="8" fill="var(--brand-blue)"/><path d="M5.2,4 L6.8,4 L7.4,6 L6.4,6.8 C6.9,8 7.9,9 9.2,9.6 L10,8.6 L12,9.2 L12,10.8 C8,11.4 4.6,8 5.2,4 Z" fill="#fff"/></svg>
      <span>877-482-6017</span>
    </li>
    <li>
      <svg class="contact-icon" viewBox="0 0 16 16"><circle cx="8" cy="8" r="8" fill="var(--brand-blue)"/><rect x="5.5" y="3.8" width="5" height="3" fill="#fff"/><rect x="4" y="7" width="8" height="3.6" rx="0.6" fill="#fff"/><rect x="5.5" y="9.4" width="5" height="2.8" fill="#fff" stroke="var(--brand-blue)" stroke-width="0.6"/></svg>
      <span>469-738-1452</span>
    </li>
    <li>
      <svg class="contact-icon" viewBox="0 0 16 16"><circle cx="8" cy="8" r="8" fill="var(--brand-blue)"/><path d="M7.9,3.4 C5.9,3.4 4.6,4.9 4.6,6.6 C4.6,8.9 7.9,12.6 7.9,12.6 C7.9,12.6 11.2,8.9 11.2,6.6 C11.2,4.9 9.9,3.4 7.9,3.4 Z" fill="#fff"/><circle cx="7.9" cy="6.6" r="1.2" fill="var(--brand-blue)"/></svg>
      <span>2847 Larkspur Blvd, Ste 300, Dallas, TX 75204</span>
    </li>
    <li>
      <svg class="contact-icon" viewBox="0 0 16 16"><circle cx="8" cy="8" r="8" fill="var(--brand-blue)"/><rect x="4" y="5" width="8" height="6" fill="#fff"/><path d="M4,5 L8,8.4 L12,5" fill="none" stroke="var(--brand-blue)" stroke-width="0.9"/></svg>
      <span>bry@bry7legal.example</span>
    </li>
    <li>
      <svg class="contact-icon" viewBox="0 0 16 16"><circle cx="8" cy="8" r="8" fill="var(--brand-blue)"/><circle cx="8" cy="8" r="4" fill="none" stroke="#fff" stroke-width="1"/><ellipse cx="8" cy="8" rx="1.8" ry="4" fill="none" stroke="#fff" stroke-width="0.9"/><line x1="4" y1="8" x2="12" y2="8" stroke="#fff" stroke-width="0.9"/></svg>
      <span>www.bry7legal.example</span>
    </li>
  </ul>
</main>
</body>
</html>
```